Web design - holistic filmmaker

I need a design for my new website.

I am a holistic filmmaker, ie I make films for healers, alternative practitioners, spiritual people and institutions that offer training in this field.

The design should be noble, bright, convey the feeling of space and expanse and have some particularly beautiful color accents.

The structure is: start page, offer, references, about me, imprint.

As an idea for the start page, I thought that either I could introduce myself as a filmmaker and my offer, or we could start right on the start page with the references, ie photos and links to already realized projects.

If you want more information or an exchange, I'd love to hear from you. At the moment I just don't know how to describe it better.

The winner will then be asked to design a logo.

Target Market(s)

healers, alternative practitioners, spiritual people and institutions that offer training in this field

Industry/Entity Type

Film production

Number of Pages Required

3 page

```html
<!DOCTYPE html>
<html lang="en">
<head>
<meta charset="utf-8">
<title>Jonas Verhoek – Creative Filmmaker</title>
<link href="https://fonts.googleapis.com/css2?family=Urbanist:wght@300;400;600;700&family=Nunito+Sans:wght@400;600&display=swap" rel="stylesheet">
<style>
:root{
  --red:#9b0a0a;
  --red-bright:#b30d0d;
  --ink:#1f1f1f;
  --ink-deep:#161616;
  --footer:#1c1c1c;
  --white:#ffffff;
  --muted:#d9d9d9;
  --badge:#d9a77a;
}
*{margin:0;padding:0;box-sizing:border-box}
html,body{width:1200px;height:4067px;overflow:hidden}
body{position:relative;background:var(--white);font-family:"Nunito Sans",sans-serif;color:var(--white)}
.section{position:absolute;left:0;width:1200px;overflow:hidden}
.photo{position:absolute}
h1,h2,.brand{font-family:"Urbanist",sans-serif}

/* hero */
.hero{top:0;height:750px}
.hero .photo{inset:0;background:radial-gradient(ellipse at 50% 45%,#b04a3c 0%,#7a2c28 45%,#3e1d1f 100%)}
.brand{position:absolute;font-weight:700;color:var(--white)}
.hero .brand{left:125px;top:40px;font-size:50px;letter-spacing:-1px}
.menu-btn{position:absolute;left:1033px;top:52px;width:40px;height:40px;border-radius:50%;background:var(--white)}
.menu-btn span{position:absolute;left:11px;width:18px;height:3px;border-radius:2px;background:var(--red)}
.hero-title{position:absolute;top:505px;width:100%;text-align:center;font-size:86px;font-weight:600;letter-spacing:-2px;line-height:1}
.hero-sub{position:absolute;top:610px;width:100%;text-align:center;font-size:27px;letter-spacing:1px;font-family:"Nunito Sans",sans-serif}

/* about */
.about{top:750px;height:750px;background:var(--ink)}
.about .portrait{left:0;top:0;width:535px;height:750px;background:linear-gradient(160deg,#9a9a9a,#4a4a4a 55%,#1e1e1e)}
.about .backdrop{left:535px;top:0;width:665px;height:750px;background:linear-gradient(180deg,#242424 0%,#262a2a 60%,#1f2222 100%)}
.about h2{position:absolute;left:602px;top:110px;font-size:56px;font-weight:600;line-height:67px;letter-spacing:-1px}
.about p{position:absolute;left:602px;width:460px;font-size:15px;line-height:26.7px}
.btn{position:absolute;display:flex;align-items:center;justify-content:center;font-size:16px;letter-spacing:3px;color:var(--white);background:var(--red)}
.about .btn{left:602px;top:597px;width:248px;height:43px}

/* quote */
.quote{top:1500px;height:750px}
.quote .panel{position:absolute;left:0;top:0;width:533px;height:750px;background:var(--red)}
.quote h2{position:absolute;left:122px;top:230px;font-size:55px;font-weight:600;line-height:68px;letter-spacing:-1px}
.quote .tagline{position:absolute;left:122px;top:462px;font-size:27px;line-height:34px}
.quote .camera{left:533px;top:0;width:334px;height:750px;background:linear-gradient(170deg,#3a3a3a,#1a1410 50%,#4a3420 75%,#111)}
.quote .face{left:867px;top:0;width:333px;height:750px;background:linear-gradient(160deg,#5b6e3a,#a88a74 40%,#3a3d44 80%)}
.quote .accent{position:absolute;left:863px;top:183px;width:9px;height:384px;background:var(--red-bright)}

/* projects */
.projects{top:2250px;height:750px;background:#111}
.projects .p1{left:0;top:0;width:400px;height:750px;background:linear-gradient(180deg,#2d4a66,#4a3a30 55%,#111)}
.projects .p2{left:400px;top:0;width:400px;height:750px;background:linear-gradient(180deg,#4a5a3a,#7a6a66 50%,#141414)}
.projects .p3{left:800px;top:0;width:400px;height:750px;background:linear-gradient(180deg,#5a4a40,#5e3a4e 55%,#121212)}
.projects .shade{position:absolute;left:0;top:0;width:1200px;height:750px;background:linear-gradient(180deg,rgba(0,0,0,0) 40%,rgba(0,0,0,.75) 100%)}
.projects h2{position:absolute;top:465px;width:100%;text-align:center;font-size:57px;font-weight:600;letter-spacing:-1px}
.projects p{position:absolute;left:300px;top:433px;margin-top:120px;width:600px;text-align:center;font-size:15px;line-height:20px;text-transform:uppercase}
.projects .btn{left:477px;top:628px;width:248px;height:44px}

/* newsletter */
.news{top:3000px;height:750px}
.news .photo{inset:0;background:linear-gradient(100deg,#6a1a24 0%,#7d1e26 40%,#2d4a48 60%,#8a2a22 85%,#b24a30 100%)}
.news h2{position:absolute;left:125px;top:220px;font-size:56px;font-weight:600;letter-spacing:-1px}
.news .sub{position:absolute;left:125px;top:307px;font-size:21px}
.news .small{position:absolute;left:125px;top:352px;font-size:15px}
.news .field{position:absolute;left:125px;top:417px;width:463px;height:46px;background:var(--white);color:#555;font-size:14px;padding:13px 42px}
.news .btn{left:125px;top:487px;width:248px;height:43px;background:#000}

/* footer */
.footer{top:3750px;height:250px;background:var(--footer)}
.footer .brand{left:125px;top:95px;font-size:48px;font-weight:300}
.footer .rule{position:absolute;left:228px;top:123px;width:42px;height:2px;background:var(--red-bright)}
.contact{position:absolute;top:95px;display:flex;align-items:center;gap:18px}
.contact .badge{width:52px;height:52px;border-radius:50%;background:var(--badge);display:flex;align-items:center;justify-content:center}
.contact .label{font-size:9px;font-weight:600;letter-spacing:3px;text-transform:uppercase}
.contact .value{font-size:16px;line-height:24px}
.copyright{position:absolute;top:4000px;left:0;width:1200px;height:67px;background:var(--white);color:#555;font-size:15px;text-align:center;line-height:67px}
</style>
</head>
<body>

<section class="section hero">
  <div class="photo" role="img" aria-label="Filmmaker operating a camera on set at dusk, red-tinted"></div>
  <div class="brand">JV</div>
  <div class="menu-btn"><span style="top:13px"></span><span style="top:19px"></span><span style="top:25px"></span></div>
  <h1 class="hero-title">Jonas Verhoek</h1>
  <div class="hero-sub">CREATIVE FILMMAKER</div>
</section>

<section class="section about">
  <div class="photo portrait" role="img" aria-label="Black and white portrait of the filmmaker smiling"></div>
  <div class="photo backdrop" role="img" aria-label="Dim film crew scene on a beach"></div>
  <h2>I Am A Holistic<br>Filmmaker.</h2>
  <p style="top:265px">My name is Jonas and I do movies - with enthusiasm and wholeheartedly. I am a holistic<br>filmmaker. At the end of the 1990s, I was faced with the question of whether I should go into alternative medicine or the film industry as a career. Professionally, I chose film at that time, but the spiritual and my passion for the so-called alternative healing methods have accompanied me almost as intensely ever since.</p>
  <p style="top:478px">My cinematic path literally brought me from cable guy to cameraman, director and producer. It all started in 1995 as a camera assistant for the US news agency NVA.</p>
  <div class="btn">Read More</div>
</section>

<section class="section quote">
  <div class="panel"></div>
  <h2>The<br>Production Of<br>Your Film</h2>
  <div class="tagline">IS ALWAYS ALSO A<br>JOURNEY TO YOURSELF.</div>
  <div class="photo camera" role="img" aria-label="Close-up of a professional video camera with monitor"></div>
  <div class="photo face" role="img" aria-label="Portrait of the filmmaker outdoors"></div>
  <div class="accent"></div>
</section>

<section class="section projects">
  <div class="photo p1" role="img" aria-label="Still from a recent film project"></div>
  <div class="photo p2" role="img" aria-label="Still from a recent film project"></div>
  <div class="photo p3" role="img" aria-label="Still from a recent film project"></div>
  <div class="shade"></div>
  <h2>My Recent Projects</h2>
  <p>As a full-service provider, I offer everything from one source, from consulting and conception to the finished film.</p>
  <div class="btn">View All</div>
</section>

<section class="section news">
  <div class="photo" role="img" aria-label="Camera operator adjusting a film camera, red and teal light"></div>
  <h2>Stay In The Know!</h2>
  <div class="sub">FOR OUR LATEST UPDATES</div>
  <div class="small">Documentary advertising films that are close to the people</div>
  <div class="field">Email</div>
  <div class="btn">Subscrobe</div>
</section>

<footer class="section footer">
  <div class="brand">JV</div>
  <div class="rule"></div>
  <div class="contact" style="left:305px">
    <div class="badge"><svg width="20" height="16" viewBox="0 0 20 16"><rect x="1" y="1" width="18" height="14" rx="2" fill="#5a3b25"/><path d="M2 3l8 6 8-6" stroke="#d9a77a" stroke-width="1.6" fill="none"/></svg></div>
    <div><div class="label">Email:</div><div class="value">info@verhoekfilm.com</div></div>
  </div>
  <div class="contact" style="left:558px">
    <div class="badge"><svg width="20" height="20" viewBox="0 0 24 24"><path d="M6.6 10.8a15 15 0 006.6 6.6l2.2-2.2a1 1 0 011-.25 11.4 11.4 0 003.6.6 1 1 0 011 1V20a1 1 0 01-1 1A17 17 0 013 4a1 1 0 011-1h3.5a1 1 0 011 1c0 1.25.2 2.45.6 3.6a1 1 0 01-.25 1z" fill="#5a3b25"/></svg></div>
    <div><div class="label">Phone:</div><div class="value">0000-555-123</div></div>
  </div>
  <div class="contact" style="left:808px">
    <div class="badge"><svg width="18" height="22" viewBox="0 0 18 22"><path d="M9 1a7 7 0 00-7 7c0 5.3 7 13 7 13s7-7.7 7-13a7 7 0 00-7-7z" fill="#5a3b25"/><circle cx="9" cy="8" r="2.6" fill="#d9a77a"/></svg></div>
    <div><div class="label">Address:</div><div class="value" style="font-size:14px">Lorem Ipsum is simply<br>dummy text of the printing</div></div>
  </div>
</footer>

<div class="copyright">Copyright © 2023 jonas verhoek. All right reserved</div>

</body>
</html>
```